Construction material supplies company business card ****

1. Full company name “K T Masonry Works Ltd”
I am after a Business card design for the company as a whole. We are better known in Solomon Islands as “K T Masonry” for short.

We are a building materials supplier of
Ready Mixed Concrete, Bricks and Blocks,
Quarry products- gravel, aggregates, sand etc.
Cement distributor/retailer of reputable brands.
Other prefab concrete products. Culverts, wave breakers, concrete retaining blocks etc.

2. Competitive Advantage over Competition: Quality, efficient, professional, dependable, reliable

3. We want people to feel trust worthy, high quality, strong when they see our brand

5. No preference to color. Maybe more sturdy and corporate. Not fancy.

Industry/Entity Type

CONSTRUCTION SUPPLY

Contact Information for Business Card

Name, Position, office phone mob phone, email

Requirements
Must have
• the company logo
Nice to have
• would like to see a mixture of designs, of with logo only and also with simple graphic designs to bring out the company whilst still have the strong sturdy professional feeling

```html
<!DOCTYPE html>
<html lang="en">
<head>
<meta charset="utf-8">
<title>K T Masonry – Business Card</title>
<link rel="stylesheet" href="https://fonts.googleapis.com/css2?family=Roboto:wght@400;500;700&display=swap">
<style>
  :root {
    --backdrop: #2b2b2b;
    --navy: #1a3c62;
    --navy-deep: #15304f;
    --steel: #34567d;
    --steel-light: #3f6189;
    --band: rgba(16, 38, 68, 0.72);
    --edge: #3a3d42;
    --concrete: #e4e4e4;
    --concrete-light: #f1f1f1;
    --ink: #1d3d62;
    --ink-soft: #2c4566;
    --white: #ffffff;
    --text-light: #e9eef5;
  }
  * { margin: 0; padding: 0; box-sizing: border-box; }
  html, body { width: 1200px; height: 1138px; overflow: hidden; }
  body {
    background: var(--backdrop);
    font-family: "Roboto", Arial, sans-serif;
    position: relative;
  }
  .card {
    position: absolute;
    border-radius: 16px;
    overflow: hidden;
  }

  /* Front */
  .card-front {
    left: 274px; top: 186px; width: 623px; height: 376px;
    background: linear-gradient(160deg, var(--steel-light) 0%, var(--steel) 45%, #2c4a70 100%);
  }
  .front-brand {
    position: absolute; left: 0; right: 0; top: 70px;
    display: flex; align-items: center; justify-content: center; gap: 20px;
  }
  .brand-square {
    width: 58px; height: 58px;
    border: 6px solid var(--white);
  }
  .brand-name {
    color: var(--white);
    font-weight: 700;
    letter-spacing: 2px;
    text-transform: uppercase;
    line-height: 1;
  }
  .front-brand .brand-name { font-size: 52px; }
  .intro-pill {
    position: absolute; left: 138px; top: 186px; width: 346px; height: 38px;
    border-radius: 19px;
    background: var(--steel);
    border: 2px solid rgba(20, 45, 78, 0.7);
    color: var(--text-light);
    font-size: 16px;
    display: flex; align-items: center; justify-content: center;
    z-index: 2;
  }
  .product-band {
    position: absolute; left: 0; right: 0; top: 214px; height: 78px;
    background: var(--band);
  }
  .front-line {
    position: absolute; left: 0; right: 0;
    text-align: center;
    color: var(--text-light);
    font-size: 16px;
    white-space: nowrap;
  }

  /* Back */
  .card-back {
    left: 276px; top: 608px; width: 618px; height: 374px;
    background: linear-gradient(135deg, var(--concrete) 0%, var(--concrete-light) 55%, #dcdcdc 100%);
  }
  .back-shapes { position: absolute; left: 0; top: 0; }
  .back-brand {
    position: absolute; left: 0; width: 300px; top: 220px;
    text-align: center;
  }
  .back-brand .brand-name { font-size: 33px; }
  .contact {
    position: absolute; left: 349px; top: 66px;
    color: var(--ink-soft);
  }
  .contact-name {
    font-size: 23px; font-weight: 700; color: var(--ink);
    line-height: 26px;
  }
  .contact-role { font-size: 17px; margin-top: 2px; }
  .contact-list { list-style: none; margin-top: 24px; }
  .contact-list li {
    display: flex; align-items: center; gap: 16px;
    font-size: 17px; height: 25px;
  }
  .contact-list svg { width: 16px; height: 16px; fill: var(--ink); }
  .contact-address { font-size: 17px; line-height: 26px; margin-top: 6px; }
  .tagline {
    position: absolute; left: 268px; top: 318px; height: 39px;
    display: flex; align-items: center;
    color: var(--text-light); font-size: 16.5px;
  }
</style>
</head>
<body>

<section class="card card-front" aria-label="Business card front">
  <div class="front-brand">
    <span class="brand-square"></span>
    <span class="brand-name">K T Masonry</span>
  </div>
  <div class="product-band"></div>
  <p class="intro-pill">We are a building materials supplier of</p>
  <p class="front-line" style="top:240px">Ready Mixed Concrete, Bricks and Blocks, Quarry Products</p>
  <p class="front-line" style="top:262px">Quarry Products:- Gravel, Aggregates, Sand Etc.</p>
  <p class="front-line" style="top:306px">Cement Distributor/Retailer of Reputable Brands.</p>
  <p class="front-line" style="top:331px">Other Concrete Products Culverts, Wave Breakers, Concrete Retaining Blocks</p>
</section>

<section class="card card-back" aria-label="Business card back">
  <svg class="back-shapes" width="618" height="374" viewBox="0 0 618 374">
    <path d="M0 0 H258 C360 80 360 270 262 357 L245 374 H0 Z" fill="var(--edge)"/>
    <path d="M0 0 H236 C336 80 336 270 240 357 L232 374 H0 Z" fill="var(--navy)"/>
    <rect x="240" y="318" width="378" height="39" fill="var(--navy)"/>
    <path d="M200 357 H618 V374 H190 Z" fill="var(--navy)" opacity="0"/>
  </svg>

  <div class="back-brand">
    <span class="brand-name">K T Masonry</span>
  </div>

  <div class="contact">
    <p class="contact-name">Daniel Rourke</p>
    <p class="contact-role">Managing Director</p>
    <ul class="contact-list">
      <li>
        <svg viewBox="0 0 16 16" aria-hidden="true"><path d="M1 5c0-2 3-3 7-3s7 1 7 3v1h-4V5H5v1H1z M4 7h8l2 6H2z"/></svg>
        000 0000 0000
      </li>
      <li>
        <svg viewBox="0 0 16 16" aria-hidden="true"><path d="M1 3h14v10H1z M2.5 4.5 8 9l5.5-4.5v-0.5h-11z" fill-rule="evenodd"/></svg>
        daniel@ktmasonry.com
      </li>
      <li>
        <svg viewBox="0 0 16 16" aria-hidden="true"><path d="M8 1a7 7 0 1 0 0 14A7 7 0 0 0 8 1zm0 1.5c.9 1.2 1.5 3 1.6 4.8H6.4C6.5 5.5 7.1 3.7 8 2.5zM2.6 7.3a5.5 5.5 0 0 1 2.6-4.1c-.6 1.2-1 2.6-1.1 4.1zm0 1.4h1.5c.1 1.5.5 2.9 1.1 4.1a5.5 5.5 0 0 1-2.6-4.1zM8 13.5c-.9-1.2-1.5-3-1.6-4.8h3.2c-.1 1.8-.7 3.6-1.6 4.8zm2.8-.7c.6-1.2 1-2.6 1.1-4.1h1.5a5.5 5.5 0 0 1-2.6 4.1zm1.1-5.5c-.1-1.5-.5-2.9-1.1-4.1a5.5 5.5 0 0 1 2.6 4.1z"/></svg>
        www.ktmasonry.com
      </li>
    </ul>
    <p class="contact-address">234 Anywhere St., Any City,<br>Any Town, US 123456</p>
  </div>

  <p class="tagline">Efficient, Professional, Dependable, Reliable</p>
</section>

</body>
</html>
```